Business Card Design Project : Ridgeline Press

In preparation for market launch, Tamarind's Ridgeline Press require the development of a business card. Ridgeline Press is a Community online publishing web portal. We provide the the city of Whistler located in B.C. (Canada) business directories, News, Classified ads, News, Events and blogs etc.

The main focus of the brand is to help local businesses to corporate with their online advertisement and marketing. Meeting our clients face to face is a must (B2B).

Target Market(s)

The target market is B2B customers. Business Owners to Marketing, advertising Managers

Industry/Entity Type

Business

Requirements
Must have
• - The business card will be two sided.
the BACK side will have our logo which consist of (icon, url,slogan) submited. The logo will be middle and centred.

The FRONT side should have company details:

Company Legal Name: TAMARIND RIDGELINE MEDIA

Owen Farsk
Director of Sales & Marketing

www.tamarindridgeline.biz
owen@tamarindridgeline.biz

Phone: 604 317 8842
#2714 - 582 E. Halvern St.
Vancouver, B.C. V7K2R4 Canada
Nice to have
• - For the "FRONT" side of our business card. You can separate or re-arrange with our logo components (icon, logo,slogan). It does not have to be together.

Also our company legal name is rather long so arrange or organize the name in a way to make it shorter. Your experience and creativity will have to come in play.
Should not have
• should not have other colors beside logo color and black text (2 colors). Also nothing Three dimensional

```html
<!DOCTYPE html>
<html lang="en">
<head>
<meta charset="utf-8">
<title>Tamarind Ridgeline Media – Business Card</title>
<link href="https://fonts.googleapis.com/css2?family=Arimo:wght@400;700&display=swap" rel="stylesheet">
<style>
  :root {
    --brand-blue: #3b8fd4;
    --brand-blue-deep: #1f6fc0;
    --ink: #111111;
    --paper: #ffffff;
    --paper-tint: #f3f5fa;
    --backdrop: #d9dadc;
  }
  * { box-sizing: border-box; margin: 0; padding: 0; }
  html, body {
    width: 1067px; height: 1200px; overflow: hidden;
    background: var(--backdrop);
    font-family: "Arimo", Arial, sans-serif;
  }
  .canvas { position: relative; width: 1067px; height: 1200px; }

  .card {
    position: absolute;
    left: 223px;
    width: 620px; height: 354px;
    background: var(--paper);
    overflow: hidden;
  }
  .card--back { top: 150px; }
  .card--front { top: 660px; }

  .card__texture {
    position: absolute; inset: 0;
    background: var(--paper-tint);
  }

  /* Back side */
  .brand-lockup {
    position: absolute; left: 0; right: 0; top: 110px;
    display: flex; flex-direction: column; align-items: center;
  }
  .brand-lockup__row { display: flex; align-items: center; gap: 12px; }
  .brand-lockup__dot {
    width: 22px; height: 22px; border-radius: 50%;
    background: var(--brand-blue);
  }
  .brand-lockup__url {
    font-weight: 700; font-size: 30px; color: var(--ink);
    letter-spacing: -0.2px;
  }
  .brand-lockup__slogan {
    margin-top: 4px; font-size: 20px; color: var(--brand-blue);
  }

  .stripe { position: absolute; left: 0; right: 0; }
  .card--back .stripe--black { top: 262px; height: 14px; background: var(--ink); }
  .card--back .stripe--blue { top: 286px; height: 12px; background: var(--brand-blue); }

  /* Front side */
  .company-name {
    position: absolute; left: 28px; top: 30px;
    font-weight: 700; font-size: 23px; color: var(--ink);
  }
  .contact-panel { position: absolute; left: 0; top: 70px; width: 410px; height: 160px; }
  .contact {
    position: absolute; left: 34px; top: 86px;
    color: var(--paper);
  }
  .contact__name { font-weight: 700; font-size: 17px; }
  .contact__title { font-size: 13px; margin-top: 3px; }
  .contact__line {
    display: flex; align-items: center; gap: 8px;
    font-size: 13px; margin-top: 7px;
  }
  .contact__line svg { width: 13px; height: 13px; flex: none; }
  .contact__address { font-size: 12px; margin-top: 9px; line-height: 1.3; }

  .mark-dot {
    position: absolute; left: 462px; top: 84px;
    width: 110px; height: 110px; border-radius: 50%;
    background: var(--brand-blue);
  }
  .front-url {
    position: absolute; right: 24px; top: 238px;
  }
  .front-url__url { font-weight: 700; font-size: 23px; color: var(--ink); white-space: nowrap; }
  .front-url__slogan { font-size: 15px; color: var(--brand-blue-deep); margin-top: 2px; }

  .card--front .stripe--black { top: 268px; height: 14px; right: auto; width: 280px; background: var(--ink); }
  .card--front .stripe--blue { top: 296px; height: 12px; right: 20px; background: var(--brand-blue-deep); }
</style>
</head>
<body>
<main class="canvas">

  <section class="card card--back" aria-label="Business card, back side">
    <div class="card__texture" role="img" aria-label="Faint repeating light-blue background pattern"></div>
    <div class="brand-lockup">
      <div class="brand-lockup__row">
        <span class="brand-lockup__dot"></span>
        <span class="brand-lockup__url">www.tamarindridgeline.biz</span>
      </div>
      <div class="brand-lockup__slogan">Your information gateway</div>
    </div>
    <div class="stripe stripe--black"></div>
    <div class="stripe stripe--blue"></div>
  </section>

  <section class="card card--front" aria-label="Business card, front side">
    <div class="card__texture" role="img" aria-label="Faint repeating light-blue background pattern"></div>

    <div class="company-name">Tamarind Ridgeline Media</div>

    <svg class="contact-panel" viewBox="0 0 410 160" preserveAspectRatio="none" aria-hidden="true">
      <defs>
        <linearGradient id="panelFill" x1="0" y1="0" x2="1" y2="1">
          <stop offset="0" stop-color="#2a7cc9"/>
          <stop offset="1" stop-color="#1f6fc0"/>
        </linearGradient>
      </defs>
      <polygon points="0,0 410,0 360,160 0,160" fill="url(#panelFill)"/>
    </svg>

    <div class="contact">
      <div class="contact__name">OWEN FARSK</div>
      <div class="contact__title">Director of Sales &amp; Marketing</div>
      <div class="contact__line">
        <svg viewBox="0 0 12 12" aria-hidden="true"><rect x="3" y="0.5" width="6" height="11" rx="1.2" fill="none" stroke="#fff" stroke-width="1.2"/><circle cx="6" cy="9.5" r="0.7" fill="#fff"/></svg>
        <span>604 317 8842</span>
      </div>
      <div class="contact__line">
        <svg viewBox="0 0 12 12" aria-hidden="true"><rect x="0.5" y="2.5" width="11" height="7.5" fill="#fff"/><polyline points="0.5,2.5 6,7 11.5,2.5" fill="none" stroke="#1f6fc0" stroke-width="1"/></svg>
        <span>owen@tamarindridgeline.biz</span>
      </div>
      <div class="contact__address">
        #2714 - 582 E. Halvern St.<br>
        Vancouver, B.C. V7K2R4 Canada
      </div>
    </div>

    <div class="mark-dot"></div>

    <div class="front-url">
      <div class="front-url__url">www.tamarindridgeline.biz</div>
      <div class="front-url__slogan">Your information gateway</div>
    </div>

    <div class="stripe stripe--black"></div>
    <div class="stripe stripe--blue"></div>
  </section>

</main>
</body>
</html>
```